Business Cards for company that supports physicians that do medical research

Need to create a business card for Qorvel Studies (www.qorvelstudies.example), a company devoted to supporting physicians who conduct medical research. The form of the card should match the message of research and information quest. I have provided the logo of the company as an uploaded file. Designs should be simple and slick aimed at very high end clients.

Target Market(s)

Medical doctors that are also researchers

Industry/Entity Type

Medical

Contact Information for Business Card

Should feature logo and fields for personal info:
Name/title
Phone /email

Font styles to use
Serif
Sans Serif

Requirements
Must have
• Qorvel logo and fields for personal info:
• Name: Bertrand Okonfu
• Title: VP Research and Senior Analyst
• Phone: 555-203-4719
• email: info@qorvelstudies.example
Nice to have
• Interesting cards that I've seen:
• 1- all black/charcoal or very dark background
• 2- Plastic - semi-transparent
• 3- non-standard height-width ratios
• 4- Functional cards -- USB drive incorporated
Should not have
• Too busy; needs to stay very simple

```html
<!DOCTYPE html>
<html lang="en">
<head>
<meta charset="utf-8">
<title>Qorvel Studies – Business Card</title>
<link rel="stylesheet" href="https://fonts.googleapis.com/css2?family=Open+Sans:ital,wght@0,400;0,600;0,700;1,400&display=swap">
<style>
  :root {
    --stage: #3a3a3a;
    --card-front: #f7f7f7;
    --brand-blue: #1f7cc3;
    --brand-green: #3fae49;
    --text-dark: #4a4a4a;
    --white: #ffffff;
  }
  * { margin: 0; padding: 0; box-sizing: border-box; }
  html, body {
    width: 1200px; height: 750px; overflow: hidden;
    background: var(--stage);
    font-family: "Open Sans", sans-serif;
  }
  .stage { position: relative; width: 1200px; height: 750px; }
  .card {
    position: absolute; top: 228px;
    width: 461px; height: 262px; overflow: hidden;
  }
  .card--front { left: 124px; background: var(--card-front); }
  .card--back {
    left: 618px; background: var(--brand-blue); color: var(--white);
    display: flex; flex-direction: column; align-items: center; justify-content: center;
  }

  .brand {
    position: absolute; left: 28px; top: 48px;
    display: flex; align-items: center; gap: 10px;
  }
  .brand__mark {
    width: 18px; height: 18px; border-radius: 50%; background: var(--brand-green);
  }
  .brand__name {
    font-size: 30px; font-weight: 700; color: var(--brand-blue); letter-spacing: 0.5px;
  }

  .nameband {
    position: absolute; left: 0; right: 0; top: 124px; height: 49px;
    background: var(--brand-blue);
    border-top: 2px solid var(--brand-green);
    box-shadow: 0 -3px 0 var(--card-front), 0 2px 0 var(--card-front), 0 3px 0 #8fb7d9;
    padding: 5px 0 0 27px; color: var(--white);
  }
  .nameband__name { font-size: 17px; font-weight: 600; line-height: 21px; }
  .nameband__title { font-size: 12.5px; font-weight: 400; line-height: 17px; }

  .contacts {
    position: absolute; left: 27px; top: 192px; list-style: none;
    font-size: 11.5px; color: var(--text-dark);
  }
  .contacts li { display: flex; align-items: center; gap: 6px; height: 17.5px; }
  .contacts svg { width: 12px; height: 12px; fill: var(--brand-blue); flex: none; }

  .back__name { font-size: 40px; font-weight: 700; letter-spacing: 0.5px; }
  .back__site {
    margin-top: 14px; font-size: 11.5px; font-style: italic; letter-spacing: 2px;
  }
</style>
</head>
<body>
<main class="stage">
  <section class="card card--front">
    <div class="brand">
      <span class="brand__mark"></span>
      <span class="brand__name">Qorvel Studies</span>
    </div>
    <div class="nameband">
      <p class="nameband__name">Bertrand Okonfu</p>
      <p class="nameband__title">VP Research &amp; Senior Analyst</p>
    </div>
    <ul class="contacts">
      <li>
        <svg viewBox="0 0 24 24" aria-hidden="true"><path d="M6.6 10.8a15.1 15.1 0 0 0 6.6 6.6l2.2-2.2a1 1 0 0 1 1-.25 11.4 11.4 0 0 0 3.6.57 1 1 0 0 1 1 1V20a1 1 0 0 1-1 1A17 17 0 0 1 3 4a1 1 0 0 1 1-1h3.5a1 1 0 0 1 1 1c0 1.25.2 2.45.57 3.57a1 1 0 0 1-.25 1z"/></svg>
        555-203-4719
      </li>
      <li>
        <svg viewBox="0 0 24 24" aria-hidden="true"><path d="M2 5h20v14H2z M3.5 6.5 12 13l8.5-6.5" fill="none" stroke="#1f7cc3" stroke-width="2.4"/></svg>
        info@qorvelstudies.example
      </li>
      <li>
        <svg viewBox="0 0 24 24" aria-hidden="true"><circle cx="12" cy="12" r="10"/><path d="M7 8c2 0 3 1 3 3s2 2 2 4-1 3-1 4M14 4c0 2 2 3 4 3" fill="none" stroke="#ffffff" stroke-width="1.6"/></svg>
        www.qorvelstudies.example
      </li>
    </ul>
  </section>

  <section class="card card--back">
    <span class="back__name">Qorvel Studies</span>
    <span class="back__site">www.qorvelstudies.example</span>
  </section>
</main>
</body>
</html>
```